Business Card Design

New business card design

Target Market(s)

Residential & Commercial Property Managers

Industry/Entity Type

Plumbing Services

Contact Information for Business Card

Name - Rowan Keddle, title - Director, Phone Number - 0431 286 517, email - rowan@tbk-plumbing.com.au, Company ABN - 73 215 904 386,

Font styles to use
Sans Serif

Colors
0054AA
0677BA
7BADD7
CADEEF
E8F1F8

```html
<!DOCTYPE html>
<html lang="en">
<head>
<meta charset="utf-8">
<title>TBK Plumbing Services – Business Card</title>
<link rel="stylesheet" href="https://fonts.googleapis.com/css2?family=Montserrat:wght@400;500;600;700&display=swap">
<style>
  :root {
    --page-bg: #d9d4cc;
    --card-face: #ebe7e0;
    --card-dark: #232526;
    --teal: #1f93ad;
    --ink: #2b2d2f;
    --sand: #c9b99f;
    --light-text: #d9d9d9;
  }
  * { box-sizing: border-box; margin: 0; padding: 0; }
  html, body {
    width: 1200px;
    height: 1047px;
    overflow: hidden;
    background: var(--page-bg);
    font-family: "Montserrat", sans-serif;
  }
  .card {
    position: absolute;
    left: 80px;
    top: 240px;
    width: 1040px;
    height: 567px;
    border-radius: 28px;
    overflow: hidden;
    background: var(--card-face);
    box-shadow: 0 10px 30px rgba(0,0,0,0.15);
  }
  .wave-area {
    position: absolute;
    left: 0;
    right: 0;
    top: 150px;
    bottom: 0;
    background: linear-gradient(192deg,
      rgba(35,37,38,0) 0%,
      rgba(31,147,173,0.55) 22%,
      var(--card-dark) 38%,
      var(--card-dark) 100%);
  }
  .brand {
    position: absolute;
    left: 53px;
    top: 62px;
    display: flex;
    align-items: center;
    gap: 16px;
  }
  .brand-name {
    font-size: 50px;
    font-weight: 500;
    color: var(--ink);
    letter-spacing: 0.5px;
    white-space: nowrap;
  }
  .brand-dot {
    width: 22px;
    height: 22px;
    border-radius: 50%;
    background: var(--teal);
  }
  .person {
    position: absolute;
    right: 47px;
    top: 310px;
    text-align: right;
  }
  .person-name {
    font-size: 45px;
    font-weight: 700;
    color: var(--teal);
    line-height: 1;
  }
  .person-title {
    margin-top: 10px;
    font-size: 25px;
    font-weight: 400;
    color: var(--light-text);
    line-height: 1;
  }
  .abn {
    position: absolute;
    left: 47px;
    top: 462px;
    font-size: 26px;
    font-weight: 400;
    color: var(--sand);
    line-height: 41px;
  }
  .contact {
    position: absolute;
    right: 47px;
    top: 455px;
    list-style: none;
    text-align: right;
  }
  .contact-item {
    display: flex;
    align-items: center;
    justify-content: flex-end;
    gap: 12px;
    font-size: 25px;
    font-weight: 400;
    color: var(--light-text);
    line-height: 41px;
    white-space: nowrap;
  }
  .contact-icon {
    width: 22px;
    height: 22px;
    flex: none;
  }
</style>
</head>
<body>
  <article class="card">
    <div class="wave-area" role="img" aria-label="Curved teal and charcoal wave decoration across the lower card"></div>

    <div class="brand">
      <span class="brand-name">TBK Plumbing Services</span>
      <span class="brand-dot"></span>
    </div>

    <div class="person">
      <p class="person-name">Rowan Keddle</p>
      <p class="person-title">Director</p>
    </div>

    <p class="abn">Company ABN<br>- 73 215 904 386</p>

    <ul class="contact">
      <li class="contact-item">0431 286 517
        <svg class="contact-icon" viewBox="0 0 24 24" aria-hidden="true">
          <path fill="var(--teal)" d="M6.6 10.8a15 15 0 0 0 6.6 6.6l2.2-2.2a1 1 0 0 1 1-.25 11.4 11.4 0 0 0 3.6.57 1 1 0 0 1 1 1V20a1 1 0 0 1-1 1A17 17 0 0 1 3 4a1 1 0 0 1 1-1h3.5a1 1 0 0 1 1 1c0 1.25.2 2.45.57 3.570a1 1 0 0 1-.25 1z"/>
        </svg>
      </li>
      <li class="contact-item">rowan@tbk-plumbing.com.au
        <svg class="contact-icon" viewBox="0 0 24 24" aria-hidden="true">
          <rect x="2" y="5" width="20" height="14" rx="2" fill="var(--teal)"/>
          <path d="M3 6.5l9 6.5 9-6.5" fill="none" stroke="var(--card-dark)" stroke-width="1.6"/>
        </svg>
      </li>
    </ul>
  </article>
</body>
</html>
```